Website redesign www.marigoldlawpc.com law firm site

Need to redesign the website that I currently have to look more modern and professional. Would also like to be able to make updates and post without having a huge hassle. See current www.marigoldlawpc.com. I just think that it looks very immature and it's very templated there's no ability for me to make posts or Add links or anything like that

Target Market(s)

California people looking for a powerhouse attorney in

Industry/Entity Type

Legal

Number of Pages Required

3 page

Font styles to use
Serif
Sans Serif

Colors
ec1f27
000000
ffffff

Requirements
Must have
• Must be mobile friendly. Must look professional and have ability to post links to other websites. Must have ability to post blogs or articles. Would like to be able to read my FeeTrove account and also have the ability to upload forms for people to download
Nice to have
• Simple design easy to use and not cluttered with too much text

```html
<!DOCTYPE html>
<html lang="en">
<head>
<meta charset="utf-8">
<title>Marigold Law P.C.</title>
<link rel="stylesheet" href="https://fonts.googleapis.com/css2?family=Cinzel:wght@400;700&family=Lora:ital,wght@0,400;0,700;1,400&family=Roboto:wght@400;500;700&display=swap">
<style>
:root{
  --red:#ec1f27;
  --red-dark:#b5121a;
  --black:#000000;
  --ink:#1e1e1e;
  --text:#444444;
  --muted:#777777;
  --line:#dddddd;
  --white:#ffffff;
  --footer:#1c1c1c;
  --grey-band:#8c8c8c;
}
*{box-sizing:border-box;margin:0;padding:0}
html,body{width:1200px;height:3080px;overflow:hidden;background:var(--white)}
body{font-family:"Roboto",Arial,sans-serif;color:var(--text);position:relative}
.abs{position:absolute}

/* header */
.site-header{position:absolute;left:0;top:0;width:1200px;height:107px}
.brand{left:121px;top:22px;font-family:"Cinzel",Georgia,serif;font-size:44px;color:var(--red);font-weight:400;letter-spacing:1px}
.contact-top{top:30px;display:flex;align-items:center;gap:12px;font-size:16px;color:var(--ink)}
.icon-dot{width:32px;height:32px;border-radius:50%;background:var(--red);display:flex;align-items:center;justify-content:center}

/* nav */
.main-nav{position:absolute;left:0;top:107px;width:1200px;height:43px;background:var(--black)}
.main-nav ul{list-style:none;display:flex;position:absolute;left:99px;top:0;height:43px}
.main-nav li{height:43px;display:flex;align-items:center;justify-content:center;font-family:"Cinzel",Georgia,serif;font-size:15px;color:var(--white);border-right:1px solid #333}
.main-nav li.active{background:var(--red)}

/* hero */
.hero{position:absolute;left:0;top:150px;width:1200px;height:512px;background:linear-gradient(120deg,#3a3a3e 0%,#8d8780 35%,#d8d2c8 55%,#6e6860 80%,#2c2c30 100%)}
.hero-caption{position:absolute;left:0;bottom:0;width:1200px;height:78px;background:rgba(20,20,20,.72);color:var(--white);font-family:"Cinzel",Georgia,serif;font-size:24px;text-align:center;line-height:34px;padding-top:6px;letter-spacing:.5px}
.slide-arrow{position:absolute;top:230px;width:34px;height:30px;background:#111;display:flex;align-items:center;justify-content:center}

/* welcome */
.section-title{position:absolute;left:0;width:1200px;text-align:center;font-family:"Lora",Georgia,serif;font-size:36px;color:var(--ink)}
.section-title span{color:var(--red)}
.intro{left:100px;top:770px;width:1000px;text-align:center;font-size:14px;line-height:23px;color:var(--text)}
.btn-dark{left:531px;top:860px;width:138px;height:38px;background:#2b2b2b;color:var(--white);font-size:16px;display:flex;align-items:center;justify-content:center}
.pillar{position:absolute;top:945px;width:280px;text-align:center}
.pillar h3{font-family:"Lora",Georgia,serif;font-weight:400;font-size:28px;color:var(--ink)}
.pillar .badge{width:88px;height:88px;border-radius:50%;background:var(--red);margin:20px auto 18px;display:flex;align-items:center;justify-content:center}
.pillar p{font-size:13px;line-height:19px;color:var(--text)}

/* practice */
.practice{position:absolute;left:0;top:1215px;width:1200px;height:559px;background:linear-gradient(135deg,#a8101a 0%,#d81f28 40%,#b8141c 70%,#8e0c14 100%)}
.practice h2{position:absolute;top:30px;width:1200px;text-align:center;font-family:"Lora",Georgia,serif;font-weight:400;font-size:34px;color:var(--white)}
.area{position:absolute;color:var(--white);width:230px}
.area h4{font-family:"Lora",Georgia,serif;font-size:18px;font-weight:700}
.area p{font-size:12px;line-height:16px}
.area.left{text-align:right}
.area.center{text-align:center}
.practice-brand{position:absolute;left:0;top:398px;width:1200px;text-align:center;font-family:"Cinzel",Georgia,serif;font-size:40px;line-height:54px;color:var(--white);white-space:nowrap}
.practice-rule{position:absolute;left:440px;top:462px;width:320px;height:2px;background:var(--white)}

/* blog */
.post{position:absolute;top:1930px;width:478px}
.date{position:absolute;left:0;top:0;width:62px;height:48px;background:var(--red);color:var(--white);text-align:center;font-size:14px;font-weight:700;line-height:20px;padding-top:4px}
.date small{display:block;font-weight:400;font-size:12px;line-height:16px}
.post h3{position:absolute;left:76px;top:0;width:400px;font-family:"Lora",Georgia,serif;font-weight:400;font-size:20px;line-height:26px;color:var(--ink)}
.post .thumb{position:absolute;left:0;top:72px;width:478px;height:172px;border:4px solid #e7e7e7}
.post p{position:absolute;left:0;top:256px;width:478px;font-size:13px;line-height:19px;color:var(--text)}
.dots{position:absolute;top:2272px;left:568px;display:flex;gap:9px}
.dots i{width:9px;height:9px;border-radius:50%;background:#ccc}
.dots i.on{background:var(--red)}

/* reviews */
.rule{position:absolute;left:0;top:2338px;width:1200px;height:1px;background:var(--line)}
.col-title{position:absolute;top:2385px;font-family:"Cinzel",Georgia,serif;font-size:32px;color:var(--ink);letter-spacing:.5px}
.col-title span{color:var(--red)}
.title-line{position:absolute;top:2432px;height:2px;background:#d9d9d9}
.mini-nav{position:absolute;top:2394px;display:flex;gap:6px}
.mini-nav i{width:16px;height:16px;border-radius:50%;border:1px solid #bbb}
.mini-nav i.on{border-color:var(--red)}
.quote{left:760px;top:2455px;width:345px;font-family:"Lora",Georgia,serif;font-style:italic;font-size:14px;line-height:22px;color:#555}

/* newsletter */
.newsletter{position:absolute;left:0;top:2657px;width:1200px;height:70px;background:var(--grey-band)}
.newsletter .lead{position:absolute;left:0;top:0;height:70px;width:540px;background:#6f6f6f;clip-path:polygon(0 0,510px 0,540px 35px,510px 70px,0 70px)}
.newsletter h2{position:absolute;left:160px;top:15px;font-family:"Cinzel",Georgia,serif;font-weight:400;font-size:32px;color:var(--white)}
.nl-input{position:absolute;left:560px;top:17px;width:378px;height:38px;background:var(--white);font-size:14px;color:#888;padding:10px 12px}
.nl-btn{position:absolute;left:950px;top:17px;width:153px;height:38px;background:var(--red);color:var(--white);font-size:17px;font-weight:500;display:flex;align-items:center;justify-content:center}

/* footer */
.site-footer{position:absolute;left:0;top:2750px;width:1200px;height:287px;background:var(--footer);color:#cfcfcf}
.foot-title{position:absolute;top:40px;font-family:"Cinzel",Georgia,serif;font-size:17px;color:var(--white)}
.foot-title span{color:var(--red)}
.quick{position:absolute;left:97px;top:80px;list-style:none;font-size:13px;line-height:27px}
.quick li::before{content:"•";color:var(--red);margin-right:8px}
.quick li.active{color:var(--red)}
.contact-list{position:absolute;left:275px;top:80px;font-size:13px;line-height:27px}
.contact-list b{color:var(--white);font-weight:500;font-size:14px}
.contact-list div{display:flex;align-items:center;gap:10px}
.map{position:absolute;left:570px;top:90px;width:245px;height:105px;background:linear-gradient(135deg,#e8e4da,#cfd6c8 50%,#e2ddd0)}
.foot-brand{position:absolute;left:860px;top:95px;width:240px;text-align:center;font-family:"Cinzel",Georgia,serif;font-size:23px;color:var(--red);white-space:nowrap}
.pay-card{position:absolute;left:880px;top:150px;width:200px;height:90px;background:var(--white);border-radius:4px;text-align:center;padding-top:14px}
.pay-card .name{font-weight:700;font-size:22px;color:var(--ink)}
.pay-card .cards{display:flex;gap:8px;justify-content:center;margin-top:12px}
.pay-card .cards i{width:36px;height:22px;border-radius:3px;background:#c9c9c9}
.bottom-bar{position:absolute;left:0;top:3037px;width:1200px;height:43px;background:var(--red);color:var(--white);font-size:13px}
.bottom-bar .copy{position:absolute;left:97px;top:13px}
.follow{position:absolute;right:97px;top:8px;display:flex;align-items:center;gap:9px}
.follow i{width:27px;height:27px;border-radius:50%;background:rgba(255,255,255,.9)}
</style>
</head>
<body>

<header class="site-header">
  <div class="abs brand">Marigold Law P.C.</div>
  <div class="abs contact-top" style="left:655px">
    <span class="icon-dot"><svg width="16" height="16" viewBox="0 0 24 24"><path fill="#fff" d="M6.6 10.8a15 15 0 006.6 6.6l2.2-2.2c.3-.3.7-.4 1-.2 1.1.4 2.3.6 3.6.6.6 0 1 .4 1 1V20c0 .6-.4 1-1 1A17 17 0 013 4c0-.6.4-1 1-1h3.5c.6 0 1 .4 1 1 0 1.3.2 2.5.6 3.6.1.3 0 .7-.2 1z"/></svg></span>
    (530) 555-0148
  </div>
  <div class="abs contact-top" style="left:837px">
    <span class="icon-dot"><svg width="16" height="12" viewBox="0 0 20 14"><rect x="0" y="0" width="20" height="14" rx="1" fill="#fff"/><path d="M1 1l9 7 9-7" stroke="#ec1f27" stroke-width="1.6" fill="none"/></svg></span>
    dana@marigoldlawgroup.com
  </div>
</header>

<nav class="main-nav">
  <ul>
    <li class="active" style="width:119px">Home</li>
    <li style="width:218px">Attorney Profile</li>
    <li style="width:223px">Practice Areas&nbsp;▾</li>
    <li style="width:189px">Client Reviews</li>
    <li style="width:146px">Links</li>
    <li style="width:146px;border-right:0">Contact Us</li>
  </ul>
</nav>

<section class="hero" role="img" aria-label="Attorney signing a document beside a small model house">
  <div class="slide-arrow" style="left:0"><svg width="10" height="14" viewBox="0 0 10 14"><path d="M8 1L2 7l6 6" stroke="#fff" stroke-width="2" fill="none"/></svg></div>
  <div class="slide-arrow" style="right:0"><svg width="10" height="14" viewBox="0 0 10 14"><path d="M2 1l6 6-6 6" stroke="#fff" stroke-width="2" fill="none"/></svg></div>
  <div class="hero-caption">A Boutique Law Firm Opportunity For Clients Who Want To Enjoy All The<br>Advantages Of Dana's Broad Legal Experience And Education.</div>
</section>

<h2 class="section-title" style="top:690px;font-weight:400">Welcome to <span>Marigold Law P.C</span></h2>
<p class="abs intro">Marigold Law P.C. is owned by Dana L. Marigold, a dedicated and caring professional who uses her broad range of skills as a California lawyer to bring consumers and business owners exceptionally strong legal representation that achieves best results. She works with people from across the northern region of California, from the Northern border to the Central Valley region.</p>
<div class="abs btn-dark">Read More</div>

<div class="pillar" style="left:122px">
  <h3>Mission</h3>
  <div class="badge"><svg width="46" height="46" viewBox="0 0 46 46"><circle cx="21" cy="25" r="17" fill="none" stroke="#fff" stroke-width="4"/><circle cx="21" cy="25" r="9" fill="none" stroke="#fff" stroke-width="4"/><circle cx="21" cy="25" r="3" fill="#fff"/><path d="M21 25L40 6" stroke="#fff" stroke-width="3"/><path d="M36 4h6v6" stroke="#fff" stroke-width="3" fill="none"/></svg></div>
  <p>Sed ut perspiciatis unde omnis iste<br>natus error sit voluptatem accusantium<br>doloremque laudantium,</p>
</div>
<div class="pillar" style="left:460px">
  <h3>Vision</h3>
  <div class="badge"><svg width="50" height="32" viewBox="0 0 50 32"><path d="M2 16C10 4 40 4 48 16 40 28 10 28 2 16z" fill="#fff"/><circle cx="25" cy="16" r="8" fill="#ec1f27"/><circle cx="25" cy="16" r="3.5" fill="#fff"/></svg></div>
  <p>Sed ut perspiciatis unde omnis iste<br>natus error sit voluptatem accusantium<br>doloremque laudantium,</p>
</div>
<div class="pillar" style="left:794px">
  <h3>Values</h3>
  <div class="badge"><svg width="44" height="40" viewBox="0 0 44 40"><rect x="4" y="24" width="8" height="14" fill="#fff"/><rect x="16" y="18" width="8" height="20" fill="#fff"/><rect x="28" y="10" width="8" height="28" fill="#fff"/><path d="M4 16L16 8l8 4L38 2" stroke="#fff" stroke-width="3" fill="none"/></svg></div>
  <p>Sed ut perspiciatis unde omnis iste<br>natus error sit voluptatem accusantium<br>doloremque laudantium,</p>
</div>

<section class="practice">
  <h2>Practice Areas</h2>
  <svg class="abs" style="left:0;top:0" width="1200" height="559" viewBox="0 0 1200 559">
    <path d="M323 475 A285 285 0 0 1 877 475" fill="none" stroke="#fff" stroke-width="5"/>
    <g fill="#fff">
      <circle cx="600" cy="204" r="30"/>
      <circle cx="437" cy="252" r="30"/>
      <circle cx="764" cy="252" r="30"/>
      <circle cx="359" cy="354" r="30"/>
      <circle cx="841" cy="354" r="30"/>
      <circle cx="323" cy="475" r="30"/>
      <circle cx="877" cy="475" r="30"/>
    </g>
    <g fill="#ec1f27">
      <circle cx="600" cy="204" r="22"/>
      <circle cx="437" cy="252" r="22"/>
      <circle cx="764" cy="252" r="22"/>
      <circle cx="359" cy="354" r="22"/>
      <circle cx="841" cy="354" r="22"/>
      <circle cx="323" cy="475" r="22"/>
      <circle cx="877" cy="475" r="22"/>
    </g>
    <g fill="#fff">
      <circle cx="593" cy="197" r="4"/><circle cx="607" cy="197" r="4"/><rect x="587" y="203" width="12" height="11" rx="4"/><rect x="601" y="203" width="12" height="11" rx="4"/>
      <text x="437" y="259" font-family="Roboto,sans-serif" font-size="20" font-weight="700" text-anchor="middle">$</text>
      <circle cx="759" cy="254" r="6" fill="none" stroke="#fff" stroke-width="3"/><circle cx="770" cy="250" r="6" fill="none" stroke="#fff" stroke-width="3"/>
      <path d="M347 356l12-11 12 11h-4v10h-16v-10z"/>
      <path d="M829 362a12 12 0 0 1 24 0z"/><rect x="838" y="345" width="6" height="6"/>
      <rect x="311" y="469" width="24" height="16" rx="2"/><rect x="318" y="464" width="10" height="6" fill="none" stroke="#fff" stroke-width="2"/>
      <rect x="866" y="462" width="16" height="8" rx="2" transform="rotate(-40 874 466)"/><rect x="875" y="470" width="3" height="16" transform="rotate(-40 876 478)"/><rect x="868" y="484" width="20" height="3"/>
    </g>
  </svg>

  <div class="area center" style="left:485px;top:110px"><h4>Family Law</h4><p>Sed ut perspiciatis unde omnis<br>sit voluptatem accusantium</p></div>
  <div class="area left" style="left:170px;top:155px"><h4>Bankruptcy</h4><p>Sed ut perspiciatis unde omnis<br>sit voluptatem accusantium</p></div>
  <div class="area" style="left:805px;top:155px"><h4>Criminal Law</h4><p>Sed ut perspiciatis unde omnis<br>sit voluptatem accusantium</p></div>
  <div class="area left" style="left:80px;top:315px"><h4>Real Estate Law</h4><p>Sed ut perspiciatis unde omnis<br>sit voluptatem accusantium</p></div>
  <div class="area" style="left:880px;top:312px"><h4>Civil Litigation</h4><p>Sed ut perspiciatis unde omnis<br>sit voluptatem accusantium</p></div>
  <div class="area left" style="left:52px;top:448px"><h4>Business Law</h4><p>Sed ut perspiciatis unde omnis<br>sit voluptatem accusantium</p></div>
  <div class="area" style="left:922px;top:440px"><h4>Unlawful Detainer</h4><p>Sed ut perspiciatis unde omnis<br>sit voluptatem accusantium</p></div>
  <div class="practice-brand">Marigold Law P.C.</div>
  <div class="practice-rule"></div>
</section>

<h2 class="section-title" style="top:1822px;font-weight:400">Latest From <span>Our Blog</span></h2>

<article class="post" style="left:97px">
  <div class="date">17th<small>Feb</small></div>
  <h3>Lorem ipsum dolor sit amet, consectetuer adipiscing elit doloremque.</h3>
  <div class="thumb" role="img" aria-label="Gavel resting on a historic parchment document" style="background:linear-gradient(120deg,#d9c49a,#a8824f 45%,#6a4524 70%,#c9ad7c)"></div>
  <p>Fusce elementum, nulla vel pellentes consequat, ante nulla hendrerit arcu, ac tincidunt mauris lacus sed leo. vamus suscipit molestie vestibulum. Lorem ipsum dolor sit amet,</p>
</article>
<article class="post" style="left:626px">
  <div class="date">17th<small>Feb</small></div>
  <h3>Lorem ipsum dolor sit amet, consectetuer adipiscing elit doloremque.</h3>
  <div class="thumb" role="img" aria-label="Scales of justice and gavel on a wooden desk" style="background:linear-gradient(120deg,#3a2414,#7a4b26 40%,#b98652 60%,#4a2c16)"></div>
  <p>Fusce elementum, nulla vel pellentes consequat, ante nulla hendrerit arcu, ac tincidunt mauris lacus sed leo. vamus suscipit molestie vestibulum. Lorem ipsum dolor sit amet,</p>
</article>
<div class="dots"><i class="on"></i><i></i><i></i><i></i></div>

<div class="rule"></div>

<h2 class="col-title" style="left:80px;font-weight:400">Ratings <span>and Reviews</span></h2>
<div class="mini-nav" style="left:500px"><i></i><i class="on"></i></div>
<div class="title-line" style="left:80px;width:460px"></div>
<div class="abs" style="left:88px;top:2470px;width:96px;height:96px;border-radius:50%;background:#dfe6ef;border:3px solid #2a5da8"></div>
<div class="abs" style="left:222px;top:2462px;width:108px;height:108px;border-radius:50%;background:#e4e4e4;border:3px solid #555"></div>
<div class="abs" style="left:360px;top:2490px;width:180px;height:54px;background:#e8ecf2"></div>
<div class="abs" style="left:600px;top:2375px;width:1px;height:250px;background:var(--line)"></div>

<h2 class="col-title" style="left:655px;font-weight:400">Clients <span>Testimonials</span></h2>
<div class="mini-nav" style="left:1070px"><i></i><i class="on"></i></div>
<div class="title-line" style="left:655px;width:450px"></div>
<div class="abs" role="img" aria-label="Client portrait" style="left:655px;top:2458px;width:94px;height:94px;border-radius:50%;border:4px solid var(--red);background:linear-gradient(160deg,#c9b4a2,#6d5a4e)"></div>
<div class="abs" style="left:660px;top:2565px;font-size:14px;font-weight:700;color:var(--ink)">- Mark Feldon</div>
<p class="abs quote"><span style="color:#bbb;font-size:28px;line-height:0">“</span> Lorem ipsumn sit amet co adipisciltsed udml ier mol monk dtepor incidunt ut la dolore ma aliquanmi kni nibhmi enim nim veni exercitation ullamco ips ierr am conapik adipiscig elitsedmi do eiusmod te epo eei occuli dollurmjk oremque laudantium. amco erwere sdltnolerr am conapik adipiscig elitsedmi <span style="color:#bbb;font-size:28px;line-height:0">”</span></p>

<section class="newsletter">
  <div class="lead"></div>
  <div class="abs" style="left:97px;top:13px;width:44px;height:44px;border-radius:50%;background:var(--red);border:2px solid #fff;display:flex;align-items:center;justify-content:center"><svg width="20" height="14" viewBox="0 0 20 14"><rect width="20" height="14" rx="1" fill="#fff"/><path d="M1 1l9 7 9-7" stroke="#ec1f27" stroke-width="1.6" fill="none"/></svg></div>
  <h2>Newsletter Signup</h2>
  <div class="nl-input">Email</div>
  <div class="nl-btn">Subscribe</div>
</section>

<footer class="site-footer">
  <h3 class="foot-title" style="left:97px;font-weight:400">Quick <span>Links</span></h3>
  <ul class="quick">
    <li class="active">Home</li><li>Attorney Profile</li><li>Practice Areas</li><li>Client Reviews</li><li>Links</li><li>Contact Us</li>
  </ul>
  <h3 class="foot-title" style="left:275px;font-weight:400">Contact <span>Details</span></h3>
  <div class="contact-list">
    <b>Marigold Law, P.C. Office</b><br>
    480 Oak Avenue, Suite 310<br>
    Redding, CA 96001
    <div><svg width="14" height="14" viewBox="0 0 24 24"><path fill="#cfcfcf" d="M6.6 10.8a15 15 0 006.6 6.6l2.2-2.2c.3-.3.7-.4 1-.2 1.1.4 2.3.6 3.6.6.6 0 1 .4 1 1V20c0 .6-.4 1-1 1A17 17 0 013 4c0-.6.4-1 1-1h3.5c.6 0 1 .4 1 1 0 1.3.2 2.5.6 3.6.1.3 0 .7-.2 1z"/></svg>(530) 555-0148</div>
    <div><svg width="14" height="14" viewBox="0 0 14 14"><rect x="3" y="1" width="8" height="4" fill="#cfcfcf"/><rect x="1" y="5" width="12" height="6" rx="1" fill="#cfcfcf"/><rect x="3" y="9" width="8" height="4" fill="#888"/></svg>(888) 555-0193</div>
    <div><svg width="14" height="10" viewBox="0 0 20 14"><rect width="20" height="14" rx="1" fill="#cfcfcf"/><path d="M1 1l9 7 9-7" stroke="#1c1c1c" stroke-width="1.6" fill="none"/></svg>dana@marigoldlawgroup.com</div>
  </div>
  <h3 class="foot-title" style="left:570px;font-weight:400">Location <span>Map</span></h3>
  <div class="map" role="img" aria-label="Street map showing the office location"></div>
  <div class="foot-brand">Marigold Law P.C.</div>
  <div class="pay-card">
    <div class="name">FeeTrove</div>
    <div class="cards"><i></i><i></i><i></i></div>
  </div>
</footer>

<div class="bottom-bar">
  <div class="copy">Copyright©2016 Marigold Law, P.C. All Right Reserved.</div>
  <div class="follow">Follow Us:<i></i><i></i><i></i></div>
</div>

</body>
</html>
```